Cool Website Design Gleam Shell Crew.

We need a new website, using our existing domain, with a similar function to https://www.marbeckfilm.com/ or https://www.tolvanfinishworks.com/ instagram gleam_shell.crew.
We can send google docs with pictures.
Logo attached

```html
<!DOCTYPE html>
<html lang="en">
<head>
<meta charset="utf-8">
<title>Gleam Shell Crew — Vehicle Wraps Calgary</title>
<link href="https://fonts.googleapis.com/css2?family=Merriweather+Sans:wght@700;800&family=Lato:wght@400;700&display=swap" rel="stylesheet">
<style>
:root{
  --black:#000;
  --white:#fff;
  --blue:#1d97e8;
  --purple:#7b4ade;
  --head-blue:#2b8fe5;
  --head-purple:#6a52dc;
  --ink:#111;
  --muted:#555;
  --star:#f7c325;
  --grad:linear-gradient(90deg,var(--blue),var(--purple));
}
*{box-sizing:border-box;margin:0;padding:0}
html,body{width:1200px;height:3693px;overflow:hidden;background:var(--black)}
body{font-family:'Lato',sans-serif;color:var(--white)}
.page{position:relative;width:1200px;height:3693px;overflow:hidden;background:var(--black)}
.abs{position:absolute}
.bg-shapes{position:absolute;left:0;top:0;z-index:1}
.layer{z-index:2}
.hero-photo{left:573px;top:100px;width:627px;height:603px;z-index:0;
  background:radial-gradient(ellipse at 60% 45%,#8a2bd6 0%,#4a1380 35%,#1b0a2c 70%,#000 100%)}
.services-glow{left:0;top:1560px;width:1200px;height:300px;z-index:0;
  background:linear-gradient(180deg,#000 0%,#0e1420 50%,#000 100%)}

/* header */
.header{left:0;top:0;width:1200px;height:100px;background:var(--black);z-index:3}
.brand{left:118px;top:24px;display:flex;align-items:center;gap:10px}
.brand-mark{width:18px;height:18px;background:var(--head-blue)}
.brand-name{font-family:'Merriweather Sans',sans-serif;font-weight:800;font-size:22px;color:var(--head-blue);letter-spacing:.5px;line-height:26px;width:150px}
.nav a{position:absolute;top:42px;font-size:15px;color:var(--white);text-decoration:none;line-height:20px}
.nav .active{padding:0 26px;left:427px;top:40px;height:25px;line-height:25px;
  background:var(--grad);clip-path:polygon(12% 0,100% 0,88% 100%,0 100%)}

/* hero */
.hero-title{left:112px;top:180px;font-family:'Merriweather Sans',sans-serif;font-weight:800;font-size:34px;line-height:42px;color:var(--head-blue)}
.hero-title span{display:block;color:var(--white);font-size:34px;margin-top:6px}
.hero-text{left:112px;top:290px;width:470px;font-size:20px;line-height:30px}
.btn{position:absolute;display:flex;align-items:center;justify-content:center;font-weight:700;font-size:15px;color:var(--white);text-decoration:none}
.btn-blue{background:var(--grad)}
.btn-solid-blue{background:var(--blue)}
.btn-outline{border:1.5px solid var(--white)}
.btn-black{background:var(--black)}

/* headings */
.section-title{font-family:'Merriweather Sans',sans-serif;font-weight:800;font-size:42px;line-height:50px;
  background:linear-gradient(90deg,var(--head-blue),var(--head-purple));-webkit-background-clip:text;background-clip:text;color:transparent}
.section-text{font-size:16.5px;line-height:26px;width:560px}

/* about */
.about-photo{left:110px;top:698px;width:458px;height:393px;border:3px solid var(--white);
  background:linear-gradient(135deg,#2a3440 0%,#3c6f98 45%,#1f8ed0 75%,#0d4e80 100%)}
.about-title{left:654px;top:754px;font-family:'Merriweather Sans',sans-serif;font-weight:800;font-size:42px;line-height:50px;color:var(--white)}
.about-text{left:654px;top:824px;width:433px;font-size:16.5px;line-height:26px;text-align:justify}

/* arrows */
.arrows{display:flex;gap:8px}
.arrow{width:68px;height:45px;background:var(--grad);clip-path:polygon(28% 0,100% 0,72% 100%,0 100%);display:flex;align-items:center;justify-content:center}

/* service cards */
.card{position:absolute;top:1371px;width:310px;height:324px;background:var(--white);color:var(--ink);padding:34px 30px 0}
.card.featured{background:linear-gradient(135deg,#3f7fe0 0%,#5d6ae0 50%,#7b4ade 100%);color:var(--white)}
.card-icon{width:86px;height:60px}
.card-title{margin-top:32px;font-family:'Merriweather Sans',sans-serif;font-weight:700;font-size:19.5px;line-height:26px;white-space:nowrap}
.card-text{margin-top:12px;font-size:15.5px;line-height:26px;color:var(--muted);width:248px}
.card.featured .card-text{color:var(--white)}
.card .btn{left:30px;top:249px;width:147px;height:43px}

/* gallery */
.tile{position:absolute;width:310px;height:243px}
.tile-hover{border:3px solid var(--white);background:linear-gradient(135deg,#5aa0ee,#5f78e2 55%,#7b55dc)}
.tile-hover .btn{left:84px;top:96px;width:145px;height:43px}

/* reviews */
.review{position:absolute;top:2805px;width:310px;height:270px;background:var(--white);color:var(--ink);padding:30px 28px 0 30px}
.review-top{display:flex;justify-content:space-between;align-items:center;height:32px}
.quote{font-family:'Merriweather Sans',sans-serif;font-weight:800;font-size:52px;color:#c9c9c9;line-height:32px;height:32px;overflow:hidden;padding-top:6px}
.stars{color:var(--star);font-size:17px;letter-spacing:1px}
.review-text{margin-top:18px;font-size:15.5px;line-height:26px;color:var(--muted)}
.reviewer{position:absolute;left:28px;top:196px;display:flex;align-items:center;gap:12px}
.avatar{width:43px;height:43px;border-radius:50%;background:linear-gradient(135deg,#8a9099,#3b4048)}
.reviewer-name{font-size:16px;font-weight:700;color:var(--head-purple);line-height:18px;background:linear-gradient(90deg,var(--head-blue),var(--head-purple));-webkit-background-clip:text;background-clip:text;color:transparent}
.reviewer-role{font-size:15.5px;color:var(--muted);line-height:20px}

/* footer contact */
.footer-brand{left:112px;top:3176px;display:flex;align-items:center;gap:12px}
.footer-brand .brand-mark{background:var(--white);width:22px;height:22px}
.footer-brand .brand-name{color:var(--white);font-size:32px;line-height:40px;width:220px}
.contact-row{position:absolute;left:112px;display:flex;gap:18px;font-size:17.5px;line-height:26px}
.contact-row svg{flex:none;margin-top:3px}
.socials{left:112px;top:3508px;display:flex;gap:14px;align-items:center}
.social{width:40px;height:40px;display:flex;align-items:center;justify-content:center}
.social.active{background:var(--black)}
.social span{width:22px;height:22px;border:2.5px solid var(--white);border-radius:50%}
.contact-title{left:575px;top:3166px;font-family:'Merriweather Sans',sans-serif;font-weight:800;font-size:42px;line-height:50px;color:var(--white)}
.field{position:absolute;background:var(--white);color:#555;font-size:13.5px;padding:0 17px;display:flex;align-items:center;justify-content:space-between}
.field.area{align-items:flex-start;padding-top:12px}
.copyright{left:0;top:3642px;width:1200px;height:51px;background:var(--black);display:flex;align-items:center;justify-content:center;font-size:14px;z-index:3}
</style>
</head>
<body>
<div class="page">

  <div class="abs hero-photo" role="img" aria-label="Photo of a sedan finished in a glossy purple wrap, headlight lit"></div>
  <div class="abs services-glow"></div>

  <svg class="bg-shapes" width="1200" height="3693" viewBox="0 0 1200 3693" aria-hidden="true">
    <defs>
      <linearGradient id="bandGrad" x1="0" y1="0" x2="1" y2="0">
        <stop offset="0" stop-color="#1d97e8"/>
        <stop offset="1" stop-color="#7b4ade"/>
      </linearGradient>
    </defs>
    <polygon points="0,516 1200,770 1200,1190 0,925" fill="url(#bandGrad)"/>
    <polygon points="1200,2707 1200,3642 0,3642 0,3062" fill="url(#bandGrad)"/>
  </svg>

  <header class="abs header">
    <div class="abs brand"><span class="brand-mark"></span><span class="brand-name">GLEAM SHELL CREW</span></div>
    <nav class="nav">
      <a class="active" href="#">Home</a>
      <a style="left:551px" href="#">About Us</a>
      <a style="left:672px" href="#">Services</a>
      <a style="left:789px" href="#">Gallery</a>
      <a style="left:898px" href="#">Reviews</a>
      <a style="left:1014px" href="#">Contact Us</a>
    </nav>
  </header>

  <section class="layer">
    <h1 class="abs hero-title layer">TRANSFORM YOUR VEHICLE<span>with Precision &amp; Style</span></h1>
    <p class="abs hero-text layer">Premium wraps, seamless finishes, and meticulous attention to detail. Elevate your vehicle with Calgary’s wrapping specialists.</p>
    <a class="btn btn-solid-blue layer" style="left:112px;top:419px;width:185px;height:43px" href="#">Book an Appointment</a>
    <a class="btn btn-outline layer" style="left:310px;top:419px;width:153px;height:43px" href="#">View Projects</a>
  </section>

  <section class="layer">
    <div class="abs about-photo layer" role="img" aria-label="Installer heating blue vinyl film on a car door"></div>
    <h2 class="abs about-title layer">About Us</h2>
    <p class="abs about-text layer">At Gleam Shell Crew, we’re passionate about transforming vehicles and delivering craftsmanship you can see and trust. What started as a love for automotive aesthetics has grown into one of Calgary’s most detail-driven vinyl wrap and custom restyling studios.</p>
    <a class="btn btn-black layer" style="left:654px;top:981px;width:146px;height:43px" href="#">Read More</a>
  </section>

  <section class="layer">
    <h2 class="abs section-title layer" style="left:112px;top:1214px">Our Services</h2>
    <p class="abs section-text layer" style="left:112px;top:1282px">From full colour changes to advanced protection films, we deliver expert craftsmanship and long-lasting results.</p>
    <div class="abs arrows layer" style="left:936px;top:1249px">
      <div class="arrow"><svg width="14" height="20" viewBox="0 0 14 20"><path d="M11 2 3 10l8 8" fill="none" stroke="#fff" stroke-width="3"/></svg></div>
      <div class="arrow"><svg width="14" height="20" viewBox="0 0 14 20"><path d="M3 2l8 8-8 8" fill="none" stroke="#fff" stroke-width="3"/></svg></div>
    </div>

    <article class="card layer" style="left:110px">
      <svg class="card-icon" viewBox="0 0 86 60" fill="none" stroke="#2b8fe5" stroke-width="2"><path d="M4 40h70v-8l-8-4-10-10H26l-10 10-10 3z"/><circle cx="22" cy="42" r="6" fill="#fff"/><circle cx="60" cy="42" r="6" fill="#fff"/><path d="M30 6v8M26 10h8M52 2v6M49 5h6"/></svg>
      <h3 class="card-title">Full Colour Change Wraps</h3>
      <p class="card-text">Lorem ipsum dolor sit amet, consec tetur adipiscing elit, sed do eius mo lore magna aliqua.</p>
      <a class="btn btn-blue" href="#">Read More</a>
    </article>
    <article class="card featured layer" style="left:445px">
      <svg class="card-icon" viewBox="0 0 86 60" fill="none" stroke="#fff" stroke-width="2"><path d="M2 40h44v-8l-6-4-8-8H16l-8 8-6 3z"/><circle cx="14" cy="42" r="5"/><circle cx="36" cy="42" r="5"/><path d="M58 8l16 6v14c0 12-8 20-16 24-8-4-16-12-16-24V14z" fill="#5d6ae0"/></svg>
      <h3 class="card-title">Paint Protection Film (PPF)</h3>
      <p class="card-text">Lorem ipsum dolor sit amet, consec tetur adipiscing elit, sed do eius mo lore magna aliqua.</p>
      <a class="btn btn-black" href="#">Read More</a>
    </article>
    <article class="card layer" style="left:782px">
      <svg class="card-icon" viewBox="0 0 86 60" fill="none" stroke="#2b8fe5" stroke-width="2"><rect x="2" y="4" width="38" height="34"/><path d="M6 32l10-14 8 10 6-6 8 10"/><path d="M40 20h16l8 10h10v14H40z"/><circle cx="50" cy="46" r="5" fill="#fff"/><circle cx="68" cy="46" r="5" fill="#fff"/></svg>
      <h3 class="card-title">Custom Graphics &amp; Decals</h3>
      <p class="card-text">Lorem ipsum dolor sit amet, consec tetur adipiscing elit, sed do eius mo lore magna aliqua.</p>
      <a class="btn btn-blue" href="#">Read More</a>
    </article>
    <article class="card layer" style="left:1116px">
      <svg class="card-icon" viewBox="0 0 86 60" fill="none" stroke="#2b8fe5" stroke-width="2"><path d="M4 40h74v-12l-8-4-6-10H20l-8 10-8 4z"/><circle cx="22" cy="42" r="6" fill="#fff"/><circle cx="62" cy="42" r="6" fill="#fff"/></svg>
      <h3 class="card-title">Commercial Fleet Wraps</h3>
      <p class="card-text">Lorem ipsum dolor sit amet, consec tetur adipiscing elit, sed do eius mo lore magna aliqua.</p>
      <a class="btn btn-blue" href="#">Read More</a>
    </article>
  </section>

  <section class="layer">
    <h2 class="abs section-title layer" style="left:112px;top:1856px">Vehicle Wrap Gallery</h2>
    <p class="abs section-text layer" style="left:112px;top:1925px;width:520px">A showcase of the quality, detail, and craftsmanship behind every project we create.</p>
    <div class="abs arrows layer" style="left:936px;top:1891px">
      <div class="arrow"><svg width="14" height="20" viewBox="0 0 14 20"><path d="M11 2 3 10l8 8" fill="none" stroke="#fff" stroke-width="3"/></svg></div>
      <div class="arrow"><svg width="14" height="20" viewBox="0 0 14 20"><path d="M3 2l8 8-8 8" fill="none" stroke="#fff" stroke-width="3"/></svg></div>
    </div>
    <div class="tile layer" style="left:112px;top:2026px;background:linear-gradient(135deg,#30353c,#8a8f96 55%,#c23a2c)" role="img" aria-label="Gloved hand pressing vinyl with a red squeegee"></div>
    <div class="tile layer" style="left:445px;top:2026px;background:linear-gradient(135deg,#4b5158,#1d2f3e 50%,#0f5c86)" role="img" aria-label="Installer smoothing dark teal film on a car panel"></div>
    <div class="tile tile-hover layer" style="left:776px;top:2024px" role="img" aria-label="Installer wrapping a car door, shown under a blue highlight">
      <a class="btn btn-black" href="#">See Our Work</a>
    </div>
    <div class="tile layer" style="left:112px;top:2292px;background:linear-gradient(160deg,#3a3d44,#ff5a1f 45%,#c8340f 75%,#1c1c1c)" role="img" aria-label="Bright orange wrapped hood close-up"></div>
    <div class="tile layer" style="left:445px;top:2292px;background:linear-gradient(135deg,#2a1f6e,#8a58d8 45%,#3a2a8c 75%,#13254a)" role="img" aria-label="Installer applying a galaxy-print wrap"></div>
    <div class="tile layer" style="left:770px;top:2292px;background:linear-gradient(135deg,#9aa2ab,#6b7b8f 45%,#e6e8ea 80%)" role="img" aria-label="Installer fitting white film on a car door"></div>
  </section>

  <section class="layer">
    <h2 class="abs section-title layer" style="left:112px;top:2635px">What Our Customers Say</h2>
    <a class="btn btn-solid-blue layer" style="left:942px;top:2646px;width:146px;height:43px" href="#">View All</a>
    <p class="abs section-text layer" style="left:112px;top:2704px;width:560px">Our clients trust us with their vehicles because we deliver results that go beyond expectations.</p>

    <article class="review layer" style="left:110px">
      <div class="review-top"><span class="quote">“</span><span class="stars">★★★★★</span></div>
      <p class="review-text">Lorem ipsum dolor sit amet, consectr adipiscing elit, sed do eiusmod tempo incididunt ut labore et dolore magna aliqua.</p>
      <div class="reviewer"><div class="avatar" role="img" aria-label="Reviewer portrait"></div><div><div class="reviewer-name">Mara Quill</div><div class="reviewer-role">lorem ipsum</div></div></div>
    </article>
    <article class="review layer" style="left:445px">
      <div class="review-top"><span class="quote">“</span><span class="stars">★★★★★</span></div>
      <p class="review-text">Lorem ipsum dolor sit amet, consectr adipiscing elit, sed do eiusmod tempo incididunt ut labore et dolore magna aliqua.</p>
      <div class="reviewer"><div class="avatar" role="img" aria-label="Reviewer portrait"></div><div><div class="reviewer-name">Mara Quill</div><div class="reviewer-role">lorem ipsum</div></div></div>
    </article>
    <article class="review layer" style="left:779px">
      <div class="review-top"><span class="quote">“</span><span class="stars">★★★★★</span></div>
      <p class="review-text">Lorem ipsum dolor sit amet, consectr adipiscing elit, sed do eiusmod tempo incididunt ut labore et dolore magna aliqua.</p>
      <div class="reviewer"><div class="avatar" role="img" aria-label="Reviewer portrait"></div><div><div class="reviewer-name">Mara Quill</div><div class="reviewer-role">lorem ipsum</div></div></div>
    </article>
  </section>

  <footer class="layer">
    <div class="abs footer-brand layer"><span class="brand-mark"></span><span class="brand-name">GLEAM SHELL CREW</span></div>

    <div class="contact-row layer" style="top:3329px">
      <svg width="18" height="22" viewBox="0 0 18 22" fill="none" stroke="#fff" stroke-width="1.5"><path d="M9 21s7-7 7-12A7 7 0 0 0 2 9c0 5 7 12 7 12z"/><circle cx="9" cy="9" r="2.5"/></svg>
      <span>123, Gleam Shell Crew Company<br>Na 1236.</span>
    </div>
    <div class="contact-row layer" style="top:3403px">
      <svg width="18" height="20" viewBox="0 0 20 20" fill="none" stroke="#fff" stroke-width="1.5"><path d="M5 2l3 4-2 2c1 3 3 5 6 6l2-2 4 3-2 3C9 18 2 11 2 4z"/></svg>
      <span>+ 1 555 010 2040</span>
    </div>
    <div class="contact-row layer" style="top:3453px">
      <svg width="18" height="16" viewBox="0 0 20 16" fill="none" stroke="#fff" stroke-width="1.5"><rect x="1" y="1" width="18" height="14"/><path d="M1 1l9 8 9-8"/></svg>
      <span>info@gleamshellcrew.com</span>
    </div>
    <div class="abs socials layer">
      <div class="social active" aria-label="Social profile"><span></span></div>
      <div class="social" aria-label="Social profile"><span></span></div>
      <div class="social" aria-label="Social profile"><span></span></div>
      <div class="social" aria-label="Social profile"><span></span></div>
    </div>

    <h2 class="abs contact-title layer">Get in Touch</h2>
    <div class="field layer" style="left:576px;top:3246px;width:250px;height:38px">Name</div>
    <div class="field layer" style="left:839px;top:3246px;width:249px;height:38px">Email</div>
    <div class="field layer" style="left:576px;top:3299px;width:250px;height:38px">Phone</div>
    <div class="field layer" style="left:839px;top:3299px;width:249px;height:38px">Vehicle Make &amp; Model<svg width="10" height="6" viewBox="0 0 10 6"><path d="M1 1l4 4 4-4" fill="none" stroke="#2b8fe5" stroke-width="1.3"/></svg></div>
    <div class="field layer" style="left:576px;top:3351px;width:250px;height:38px">Service Interested In<svg width="10" height="6" viewBox="0 0 10 6"><path d="M1 1l4 4 4-4" fill="none" stroke="#2b8fe5" stroke-width="1.3"/></svg></div>
    <div class="field layer" style="left:839px;top:3351px;width:249px;height:38px">Upload Photos<svg width="14" height="14" viewBox="0 0 14 14" fill="none" stroke="#2b8fe5" stroke-width="1.3"><rect x="1" y="2" width="12" height="10"/><path d="M3 10l3-3 2 2 2-2 2 2"/></svg></div>
    <div class="field area layer" style="left:576px;top:3403px;width:512px;height:72px">Message / Project Details</div>
    <a class="btn btn-black layer" style="left:576px;top:3500px;width:214px;height:44px" href="#">Send Message</a>
  </footer>

  <div class="abs copyright">Copyright © 2025 Gleam Shell Crew. All rights reserved.</div>
</div>
</body>
</html>
```